Income Tax Business Cards - Updates

Need to update these business cards while keeping all the same wording but just update them and make them look nicer and more modern/ on brand with our brand.

Industry/Entity Type

finance

Contact Information for Business Card

we have multiple locations so will just need to easily be able to change the address and phone numbers

Colors

Designer to choose colors to be used in the design.

```html
<!DOCTYPE html>
<html lang="en">
<head>
<meta charset="utf-8">
<title>Ledgerline Financial Group – Business Cards</title>
<link rel="stylesheet" href="https://fonts.googleapis.com/css2?family=Montserrat:wght@500;700;800&display=swap">
<style>
  :root {
    --green: #0f5530;
    --green-dark: #0b4426;
    --red: #c8202b;
    --white: #ffffff;
    --ink: #3a3a3a;
    --bg: #e9ebe8;
  }
  * { box-sizing: border-box; margin: 0; padding: 0; }
  html, body { width: 1200px; height: 900px; overflow: hidden; }
  body {
    background: var(--bg);
    font-family: "Montserrat", Arial, sans-serif;
    position: relative;
  }
  .card {
    position: absolute;
    left: 250px;
    width: 700px;
    height: 400px;
    border-radius: 22px;
    overflow: hidden;
    box-shadow: 0 10px 28px rgba(0,0,0,.18);
  }

  /* Front */
  .card-front { top: 30px; background: var(--green); color: var(--white); }
  .brand {
    display: flex; align-items: center; gap: 12px;
    font-weight: 800; letter-spacing: .5px;
  }
  .brand-mark { width: 18px; height: 18px; border-radius: 50%; flex: none; }
  .card-front .brand {
    position: absolute; top: 88px; left: 0; right: 0;
    justify-content: center; font-size: 30px; color: var(--white);
  }
  .card-front .brand-mark { background: var(--white); }
  .pill {
    background: var(--red); color: var(--white);
    font-weight: 700; border-radius: 999px;
    display: inline-block; white-space: nowrap;
  }
  .front-pill {
    position: absolute; top: 180px; left: 50%; transform: translateX(-50%);
    font-size: 17px; padding: 9px 26px; letter-spacing: .5px;
  }
  .headline {
    font-weight: 800; text-transform: uppercase; white-space: nowrap;
    letter-spacing: 1px;
  }
  .headline .amount { color: var(--red); font-weight: 700; }
  .front-headline {
    position: absolute; bottom: 62px; left: 0; right: 0;
    text-align: center; font-size: 34px;
  }

  /* Back */
  .card-back { top: 470px; background: var(--white); }
  .back-band {
    position: absolute; top: 0; left: 0; right: 0; height: 178px;
    background: var(--green); border-bottom: 5px solid var(--red);
    color: var(--white); text-align: center;
  }
  .back-headline { margin-top: 44px; font-size: 34px; }
  .back-sub {
    margin-top: 12px; font-size: 14px; font-weight: 500; letter-spacing: .5px;
  }
  .back-pill {
    position: absolute; top: 150px; left: 50%; transform: translateX(-50%);
    font-size: 30px; font-weight: 800; padding: 8px 34px; letter-spacing: 1px;
  }
  .back-body {
    position: absolute; top: 230px; left: 0; right: 0; bottom: 0;
    display: flex; align-items: center; padding: 0 40px 20px;
  }
  .card-back .brand {
    font-size: 22px; color: var(--green); width: 290px; line-height: 1.2;
  }
  .card-back .brand-mark { background: var(--red); }
  .divider { width: 2px; height: 120px; background: var(--red); margin: 0 34px; }
  .contact { color: var(--ink); font-size: 18px; line-height: 1.45; font-style: normal; }
  .phone {
    display: flex; align-items: center; gap: 10px; margin-top: 8px;
    color: var(--green); font-weight: 700; font-size: 24px;
  }
  .phone svg { width: 20px; height: 20px; }
</style>
</head>
<body>

<section class="card card-front">
  <div class="brand"><span class="brand-mark"></span><span class="brand-name">Ledgerline Financial Group</span></div>
  <span class="pill front-pill">FILE YOUR TAXES HERE</span>
  <p class="headline front-headline">Up to <span class="amount">&amp;6000</span> Same Day Advance</p>
</section>

<section class="card card-back">
  <div class="back-band">
    <p class="headline back-headline">Up to <span class="amount">&amp;6000</span> Same Day Advance</p>
    <p class="back-sub">ON APPROVED TAX RETURNS!</p>
  </div>
  <span class="pill back-pill">FREE ESTIMATES!</span>
  <div class="back-body">
    <div class="brand"><span class="brand-mark"></span><span class="brand-name">Ledgerline Financial Group</span></div>
    <div class="divider"></div>
    <address class="contact">
      718 Maple Ridge Rd<br>
      Ste 140<br>
      Country Name AB 5625
      <span class="phone">
        <svg viewBox="0 0 24 24" aria-hidden="true"><path fill="#c8202b" d="M6.6 10.8a15.1 15.1 0 0 0 6.6 6.6l2.2-2.2a1 1 0 0 1 1-.25 11.4 11.4 0 0 0 3.6.57 1 1 0 0 1 1 1V20a1 1 0 0 1-1 1A17 17 0 0 1 3 4a1 1 0 0 1 1-1h3.5a1 1 0 0 1 1 1c0 1.25.2 2.45.57 3.57a1 1 0 0 1-.25 1z"/></svg>
        (555) 555-0142
      </span>
    </address>
  </div>
</section>

</body>
</html>
```